Harbourline Electrical Solutions

On one side. LOGO (underneath:) Commercial Industrial Residential

- NAME & CONTACT DETAILS

Marcus T. Hollings
Project Manager

(Cell icon) (441) 555-0187
(Email icon) hlelectricalsolutions@mailvento.com
(Facebook & Instagram icons )@hlelectricalsolutions

Other side: LOGO - underneath ELECTRICAL CONSTRUCTION & MAINTENANCE . LED LIGHTING & AUTOMATION . LIFE SAFETY SYSTEMS (FIRE ALARM / SECURITY) . DATA & COMMUNICATION

```html
<!DOCTYPE html>
<html lang="en">
<head>
<meta charset="utf-8">
<title>Harbourline Electrical Solutions — Business Cards</title>
<link href="https://fonts.googleapis.com/css2?family=Montserrat:wght@500;600;700&family=Work+Sans:wght@400;500&display=swap" rel="stylesheet">
<style>
  :root {
    --teal: #0f5870;
    --teal-light: #226c84;
    --teal-dark: #0b4b60;
    --rule-grey: #4b4b4b;
    --paper: #ffffff;
    --backdrop: #2a2b2d;
  }
  * { margin: 0; padding: 0; box-sizing: border-box; }
  html, body {
    width: 1200px; height: 900px; overflow: hidden;
    background: var(--backdrop);
  }
  .canvas { position: relative; width: 1200px; height: 900px; }
  .card {
    position: absolute; left: 250px; width: 700px; height: 400px;
    border-radius: 22px; overflow: hidden;
    box-shadow: 0 14px 30px rgba(0,0,0,.45);
  }

  /* ---------- Brand block ---------- */
  .brand {
    position: absolute; display: flex; align-items: center; gap: 18px;
    font-family: "Montserrat", sans-serif; font-weight: 600;
    text-transform: uppercase;
  }
  .brand__square { width: 46px; height: 46px; flex: none; }
  .brand__text { display: flex; flex-direction: column; gap: 8px; }
  .brand__name { font-size: 28px; letter-spacing: 4px; line-height: 1.15; }
  .brand__tagline {
    font-weight: 500; font-size: 13px; letter-spacing: 3.5px; line-height: 1;
  }

  /* ---------- Services side ---------- */
  .card--services {
    top: 30px;
    background: linear-gradient(120deg, var(--teal-dark) 0%, var(--teal-light) 55%, var(--teal) 100%);
    color: var(--paper);
  }
  .card--services .brand { top: 44px; left: 160px; }
  .card--services .brand__square { background: var(--paper); }

  .services {
    position: absolute; left: 110px; top: 232px; list-style: none;
    font-family: "Montserrat", sans-serif; font-weight: 600;
    font-size: 18px; letter-spacing: 2.2px; text-transform: uppercase;
    line-height: 1.45;
  }
  .services li { position: relative; padding-left: 24px; }
  .services li::before {
    content: ""; position: absolute; left: 0; top: 9px;
    width: 7px; height: 7px; border-radius: 50%; background: var(--paper);
  }

  /* ---------- Contact side ---------- */
  .card--contact { top: 470px; background: var(--paper); }
  .card--contact .brand { top: 34px; left: 50px; color: var(--teal); }
  .card--contact .brand__square { background: var(--teal); }
  .card--contact .brand__name { font-size: 26px; }

  .social {
    position: absolute; left: 50px; top: 160px;
    font-family: "Work Sans", sans-serif; font-size: 21px; color: var(--teal);
    display: flex; align-items: center; gap: 12px;
  }
  .social__square { width: 20px; height: 20px; border-radius: 4px; background: var(--teal); }

  .divider { position: absolute; left: 0; right: 0; top: 206px; height: 5px; background: var(--rule-grey); }
  .contact-band {
    position: absolute; left: 0; right: 0; top: 216px; bottom: 0;
    background: var(--teal); color: var(--paper);
  }
  .person { position: absolute; left: 50px; top: 16px; }
  .person__name {
    font-family: "Montserrat", sans-serif; font-weight: 600;
    font-size: 28px; letter-spacing: 5px; text-transform: uppercase;
  }
  .person__role { font-family: "Work Sans", sans-serif; font-size: 19px; margin-top: 2px; }
  .contact-list {
    position: absolute; left: 50px; top: 94px; list-style: none;
    font-family: "Work Sans", sans-serif; font-size: 20px; line-height: 1.55;
  }
  .contact-list li { display: flex; align-items: center; gap: 14px; }
  .contact-list svg { width: 18px; height: 18px; flex: none; }
</style>
</head>
<body>
<main class="canvas">

  <section class="card card--services" aria-label="Services side">
    <div class="brand">
      <span class="brand__square"></span>
      <span class="brand__text">
        <span class="brand__name">Harbourline<br>Electrical<br>Solutions</span>
        <span class="brand__tagline">Commercial · Industrial · Residential</span>
      </span>
    </div>
    <ul class="services">
      <li>Data &amp; Communication</li>
      <li>LED Lighting &amp; Automation</li>
      <li>Electrical Construction &amp; Maintenance</li>
      <li>Life Safety Systems (Fire Alarm / Security)</li>
    </ul>
  </section>

  <section class="card card--contact" aria-label="Contact side">
    <div class="brand">
      <span class="brand__square"></span>
      <span class="brand__text">
        <span class="brand__name">Harbourline<br>Electrical Solutions</span>
        <span class="brand__tagline">Commercial · Industrial · Residential</span>
      </span>
    </div>
    <p class="social"><span class="social__square"></span>@hlelectricalsolutions</p>
    <div class="divider"></div>
    <div class="contact-band">
      <div class="person">
        <p class="person__name">Marcus T. Hollings</p>
        <p class="person__role">Project Manager</p>
      </div>
      <ul class="contact-list">
        <li>
          <svg viewBox="0 0 24 24" aria-hidden="true"><path d="M6.6 2.5l3 3.2-1.9 2.4c1.2 2.6 3.4 4.8 6.1 6.1l2.4-1.9 3.3 3-1.6 3.6c-7.8-.4-14.1-6.7-14.5-14.5z" fill="none" stroke="#fff" stroke-width="1.8" stroke-linejoin="round"/></svg>
          (441) 555-0187
        </li>
        <li>
          <svg viewBox="0 0 24 24" aria-hidden="true"><rect x="2.5" y="5" width="19" height="14" rx="1.5" fill="none" stroke="#fff" stroke-width="1.8"/><path d="M3 6l9 7 9-7" fill="none" stroke="#fff" stroke-width="1.8"/></svg>
          hlelectricalsolutions@mailvento.com
        </li>
      </ul>
    </div>
  </section>

</main>
</body>
</html>
```